Website development company website

ABOUT COMPANY
Hi everyone! We're a Melbourne, Australia website development company in a need of a website design that will make online store merchants want to engage our services.
We specialise exclusively in Torvista e-commerce platform (https://torvista-platform.example/). What distinguishes our business from competition is that rather than designing and building brand new websites, we offer development, support and maintenance services to established websites. Maintenance and Support are the keywords representing our business.
Our potential clients are people with broken, slow and underperforming Torvista installations who need assistance getting their websites up and making sales. Our website must pass the message that we can help, and provide quick means of making contact.
DESIGN
Overall, we're looking for a slick, clean, airy, conservative design. No need to do anything crazy, try to stick to what's "standard" in website design these days and make it easy on all of us. The website is unlikely to be updated too often so it needs to look attractive and fresh first time over and after a year, too.
Attached is our new logo, which you'll be able to take the basic idea from, the colors and fonts. Though, don't use the fonts from the logo in the website, stick to the standard widely supported fonts. Additional use of Google fonts is fine.
Don't overdo it with colors, stick to conservative basic color set and only use the colors from the log for accents like headings etc. Please, don't be tempted to use the blue and orange as background of whole blocks, other than perhaps footer. Thanks.
For the images used, I'd like to stay away from a design studio/digital agency feel and lean more towards professional support and maintenance services. I'm thinking images of content merchants doing their job. Something along the lines of "We'll be taking care of the website so that you only need to care about the business".
Some ideas I like:
http://www.plumframe-pics.example/detail/photo/portrait-of-confident-male-design-professional-royalty-free-image/572048163
http://www.plumframe-pics.example/detail/photo/designer-taking-picture-of-hat-high-res-stock-photography/839207514
http://www.plumframe-pics.example/detail/photo/woman-packaging-pottery-royalty-free-image/216684093
Images of colorful shopping bags and shopping carts are over the top and not serious enough. Instead of images matching Online Shopping, I'd try going more for Stability, Reliability, Performance.
Our existing website is http://www.bravuln.example. Please, don't take design ideas from it, but it will give you a picture of the structure of our new website and content that's going to be used initially.
If you could include a basic icon set to use throughout the website, that would be great. If the icons could match our logo (attached), it would be a big plus.
ALL PAGES
Every page must contain clearly visible phone number (1300 648 907) and a Contact Us Now button, which opens an AJAX driven popup form with Name, Email, Phone and Message to be sent through.
To start with, main menu items will be Torvista, Portfolio, Contact.
At the bottom of each page, please, include a newsletter subscription form with text Subscribe to Torvista Support and Security Updates.
For the footer, I'd like to see a logo strip with the following logos in grayscale (no need to link anywhere): Torvista, QRX, DataVane, NCB. You'll find the logos on Google Images.
Standard footer columns follow. Here, I'd like to see logos in color: Torvista Certified Developer, Torvista Ceritified Solution Provider. Again, the logos are on Google Images.
No social media logos/links necessary anywhere on the website.
...and then the copyright line.
FRONT PAGE
Large slider with images that would appeal to our target audience. Keywords here would be Torvista System Audit, Torvista Performance Optimisation, Torvista Website Emergency Recovery, Torvista Development Infrastructure Hosting. We'll have a static page created for each of these to link to.
In a corner of the slider, or on the edge, can I have an overlay with logos in color (same as footer): Torvista Certified Developer, Torvista Ceritified Solution Provider.
Underneath, a number of blocks, each with an image and teaser that we'll use to link to various pages throughout the website.
PORTFOLIO PAGE
I'm thinking a single long page with a block per client, which will contain project name, description from us and a testimonial from client. Also, each block will contain a single large screenshot. No gallery or slideshow is necessary here, just one image per project.
I'll leave the layout up to you, but try to put yourself in the shoes of a potential client reviewing our past work by simply scrolling down this one page.
CONTACT US PAGE
Separate page with the same form as above, phone number (1300 648 907), email address (support@kavreo.example), address (Suite 42, Level 3|8 Wattlebrook Lane|Fernvale Heights VIC 3999), and a grayscale Google Map.
CODING UP
Coding up into static HTML/CSS/JS is equally important as the design itself. We're a website development company, we'll be integrating the theme. We will spot any issues and we will point them out.
Coded up design must be fully responsive. Enough said.
To be able to create any content in future, we'd like one extra page coded up with samples of all themed elements, lists, forms, buttons, 2, 3, 4-column layout, alerts, icons, etc. This page does not need to be designed, only coded up.
The design will be integrated into Drupal using Twig. If possible at all, try to keep it in mind when designing and coding up, and make the integration into a Drupal theme easier for us.
GOOD LUCK!
That's it. Let me know if anything needs clarifying. So far I've had a great experience with ArtFlockly. I don't doubt some great designs will emerge. Clever ideas are highly appreciated, but also make it clear you've read and followed the points in this brief. Cheers, Tom

```html
<!DOCTYPE html>
<html lang="en">
<head>
<meta charset="utf-8">
<title>Kavreo — Torvista Development, Support &amp; Maintenance</title>
<link rel="stylesheet" href="https://fonts.googleapis.com/css2?family=Raleway:wght@300;400;500;600;700&display=swap">
<style>
:root{
  --orange:#e8792a;
  --navy:#1f3e6e;
  --ink:#3a3a3a;
  --muted:#666;
  --light:#f3f3f3;
  --footer:#2f2f2f;
  --white:#fff;
}
*{box-sizing:border-box;margin:0;padding:0}
html,body{width:689px;height:1200px;overflow:hidden;background:var(--white)}
body{font-family:"Raleway",sans-serif;color:var(--ink);position:relative}
.page{position:relative;width:689px;height:1200px;overflow:hidden}
.abs{position:absolute}

/* header */
.top-rule{left:0;top:0;width:689px;height:3px;background:var(--orange)}
.contact-tab{left:443px;top:0;width:169px;height:22px;background:var(--orange);color:var(--white);font-size:6.5px;display:flex;align-items:center;justify-content:space-around;padding:0 8px}
.contact-tab span{display:flex;align-items:center;gap:4px}
.brand{left:77px;top:20px;display:flex;align-items:center;gap:8px}
.brand-mark{width:30px;height:30px;background:var(--orange)}
.brand-name{font-size:30px;font-weight:700;color:var(--navy);letter-spacing:-.5px;line-height:1}
.nav{left:278px;top:44px;font-size:6.5px;font-weight:500;letter-spacing:.2px;color:var(--ink)}
.nav a{color:inherit;text-decoration:none;display:block;text-align:center}
.nav .item{position:absolute;top:0;white-space:nowrap}
.nav .active::after{content:"";position:absolute;left:-10px;right:-10px;top:13px;height:1.5px;background:var(--navy)}

/* hero */
.hero{left:0;top:75px;width:689px;height:312px;background:linear-gradient(120deg,#c9a27a 0%,#9c7550 35%,#cfd3d6 55%,#6b5440 80%,#3c3027 100%)}
.hero-panel{left:138px;top:152px;width:415px;height:156px;background:rgba(15,15,15,.85);text-align:center;color:var(--white)}
.hero-title{margin-top:28px;font-size:29px;font-weight:300;line-height:34px;color:var(--orange);letter-spacing:.5px}
.hero-sub{margin-top:6px;font-size:14.5px;font-weight:400;line-height:21px}
.dots{margin-top:10px;display:flex;justify-content:center;gap:4px}
.dots i{width:7px;height:7px;border-radius:50%;background:var(--white)}
.dots i.on{background:var(--navy)}
.badges{display:flex;gap:5px}
.badge{width:16px;height:26px;background:var(--orange);border:2px solid #e5e5e5}
.badge.pale{background:#d9d9d9;border-color:#bbb}

/* what we do */
.section-title{width:689px;left:0;text-align:center;font-size:16px;font-weight:400;letter-spacing:.5px;color:var(--ink)}
.intro{left:189px;width:311px;top:437px;text-align:center;font-size:6.8px;line-height:13px;color:var(--ink)}
.intro em,.more{color:var(--orange);font-style:italic}
.why{width:260px;height:80px}
.why .ring{position:absolute;left:0;top:0;width:73px;height:73px;border:1.5px solid var(--orange);border-radius:50%;display:flex;align-items:center;justify-content:center}
.why h3{position:absolute;left:83px;top:-3px;font-size:15px;font-weight:400;color:var(--ink);white-space:nowrap}
.why p{position:absolute;left:83px;top:22px;width:180px;font-size:6.6px;line-height:12.8px;text-align:justify;color:var(--muted)}
.service{width:80px;text-align:center;font-size:7px;font-weight:600;letter-spacing:.3px;color:var(--ink)}
.service svg{display:block;margin:0 auto 5px}

/* solutions */
.solutions{left:0;top:680px;width:689px;height:300px;background:var(--light)}
.sol{width:162px}
.sol h4{height:34px;display:flex;align-items:flex-end;font-size:10px;font-weight:400;line-height:14px;letter-spacing:.2px;color:var(--ink)}
.sol .photo{margin-top:9px;width:162px;height:106px;border:2px solid #ddd}
.sol p{margin-top:7px;font-size:6.9px;line-height:12.8px;text-align:justify;color:var(--muted)}
.btn{margin-top:6px;display:inline-flex;align-items:center;gap:5px;background:var(--orange);color:var(--white);font-size:6.5px;padding:7px 7px;text-decoration:none}
.arrow{width:21px;height:21px;border:2px solid var(--navy);border-radius:50%;display:flex;align-items:center;justify-content:center}

/* tech strip */
.tech{left:0;top:980px;width:689px;height:101px;display:flex;align-items:center;justify-content:space-around;padding:0 60px}
.tech span{display:flex;align-items:center;gap:6px;font-size:22px;font-weight:500;color:#555}
.tech i{width:16px;height:16px;background:#8a8a8a;display:block}

/* footer */
.footer{left:0;top:1081px;width:689px;height:119px;background:var(--footer);color:var(--white);text-align:center;font-size:6.8px;line-height:12.5px}
.footer .badges{justify-content:center;margin-top:13px}
.footer address{font-style:normal;margin-top:13px}
.footer .copy{margin-top:5px}
</style>
</head>
<body>
<div class="page">
  <div class="abs top-rule"></div>
  <div class="abs contact-tab">
    <span><svg width="6" height="6" viewBox="0 0 10 10"><path d="M2 0l2 2-1 2c1 1 2 2 3 3l2-1 2 2-2 2C4 10 0 6 0 2z" fill="#fff"/></svg>1300 648 907</span>
    <span><svg width="7" height="5" viewBox="0 0 14 10"><rect width="14" height="10" fill="#fff"/><path d="M0 0l7 6 7-6" stroke="#e8792a" fill="none"/></svg>support@kavreo.example</span>
  </div>

  <div class="abs brand"><div class="brand-mark"></div><div class="brand-name">Kavreo</div></div>

  <nav class="abs nav">
    <a class="item active" style="left:11px">HOME</a>
    <a class="item" style="left:71px">ABOUT US</a>
    <a class="item" style="left:146px">TORVISTA</a>
    <a class="item" style="left:222px">PORTFOLIO</a>
    <a class="item" style="left:301px">CONTACT</a>
  </nav>

  <div class="abs hero" role="img" aria-label="Overhead view of a wooden desk with a laptop, notebook, glasses, calculator and pencils"></div>
  <div class="abs hero-panel">
    <h1 class="hero-title">KAVREO E-COMMERCE</h1>
    <p class="hero-sub">we offer development, support and maintenance services to<br>established websites.</p>
    <div class="dots"><i class="on"></i><i></i><i></i></div>
  </div>
  <div class="abs badges" style="left:631px;top:344px"><div class="badge pale"></div><div class="badge"></div></div>

  <h2 class="abs section-title" style="top:409px">WHAT WE DO</h2>
  <p class="abs intro">From support, maintenance and upgrades to redesigns, migrations and full site builds, we make your online store do what you need it to do <em>Read more...</em></p>

  <div class="abs why" style="left:75px;top:486px">
    <div class="ring"><svg width="26" height="26" viewBox="0 0 26 26"><rect x="3" y="8" width="20" height="16" fill="#3a3a3a"/><path d="M8 8V5a5 5 0 0110 0v3" stroke="#3a3a3a" stroke-width="2" fill="none"/></svg></div>
    <h3>WHY BRAVULN?</h3>
    <p>Fast Torvista-based online stores, built on time and to specification, backed by effective, focused support, means that our clients are among the happiest in the eCommerce world. <span class="more">Read more...</span></p>
  </div>
  <div class="abs why" style="left:350px;top:486px">
    <div class="ring"><svg width="26" height="26" viewBox="0 0 26 26"><circle cx="13" cy="13" r="10" fill="#8a8a8a"/></svg></div>
    <h3>WHY TORVISTA?</h3>
    <p>Torvista is the world's leading open source eCommerce platform. No other open-source or free system offers out-of-the-box functionality and search engine friendliness comparable to Torvista CE. <span class="more">Read more...</span></p>
  </div>

  <div class="abs service" style="left:223px;top:594px">
    <svg width="40" height="54" viewBox="0 0 40 54"><rect x="2" y="12" width="36" height="40" fill="#1f3e6e"/><rect x="2" y="12" width="8" height="40" fill="#e8792a"/><circle cx="24" cy="32" r="7" fill="none" stroke="#fff" stroke-width="3" stroke-dasharray="3 2"/><circle cx="24" cy="32" r="2.5" fill="#fff"/></svg>
    DEVELOPMENT
  </div>
  <div class="abs service" style="left:306px;top:594px">
    <svg width="40" height="54" viewBox="0 0 40 54"><rect x="2" y="12" width="36" height="40" fill="#1f3e6e"/><rect x="2" y="12" width="8" height="40" fill="#e8792a"/><circle cx="24" cy="32" r="8" fill="none" stroke="#fff" stroke-width="2.5"/><circle cx="24" cy="32" r="3.5" fill="none" stroke="#fff" stroke-width="2"/></svg>
    SUPPORT
  </div>
  <div class="abs service" style="left:389px;top:594px">
    <svg width="40" height="54" viewBox="0 0 40 54"><rect x="2" y="12" width="36" height="40" fill="#1f3e6e"/><rect x="2" y="12" width="8" height="40" fill="#e8792a"/><path d="M17 25l14 14M31 25L17 39" stroke="#fff" stroke-width="3"/></svg>
    MAINTENANCE
  </div>

  <section class="abs solutions">
    <h2 class="abs section-title" style="top:19px">OUR SOLUTIONS</h2>
    <div class="abs arrow" style="left:30px;top:144px"><svg width="8" height="8" viewBox="0 0 8 8"><path d="M5.5 1L2.5 4l3 3" stroke="#1f3e6e" stroke-width="1.8" fill="none"/></svg></div>
    <div class="abs arrow" style="left:638px;top:144px"><svg width="8" height="8" viewBox="0 0 8 8"><path d="M2.5 1l3 3-3 3" stroke="#1f3e6e" stroke-width="1.8" fill="none"/></svg></div>

    <article class="abs sol" style="left:76px;top:54px">
      <h4>TORVISTA SYSTEM AUDIT</h4>
      <div class="photo" role="img" aria-label="Smiling businessman in a blue shirt in a bright office" style="background:linear-gradient(135deg,#dfe6ee,#9fb6cf 60%,#c8d2dc)"></div>
      <p>Advanced solutions for customer communication and service, supply chain management, sales automation and other business.</p>
      <a class="btn">READ MORE <svg width="7" height="7" viewBox="0 0 8 8"><circle cx="4" cy="4" r="4" fill="#fff"/><path d="M3 2l2 2-2 2" stroke="#e8792a" fill="none"/></svg></a>
    </article>
    <article class="abs sol" style="left:264px;top:54px">
      <h4>TORVISTA PERFORMANCE<br>OPTIMISATION</h4>
      <div class="photo" role="img" aria-label="Hand holding a payment card in front of a blurred background" style="background:linear-gradient(135deg,#6f5a4a,#c9c3bd 55%,#8c96a0)"></div>
      <p>Advanced solutions for customer communication and service, supply chain management, sales automation and other business.</p>
      <a class="btn">READ MORE <svg width="7" height="7" viewBox="0 0 8 8"><circle cx="4" cy="4" r="4" fill="#fff"/><path d="M3 2l2 2-2 2" stroke="#e8792a" fill="none"/></svg></a>
    </article>
    <article class="abs sol" style="left:452px;top:54px">
      <h4>TORVISTA WEBSITE<br>EMERGENCY RECOVERY</h4>
      <div class="photo" role="img" aria-label="Hands using a smartphone" style="background:linear-gradient(135deg,#b08a6e,#ddd2c8 55%,#a27e64)"></div>
      <p>Advanced solutions for customer communication and service, supply chain management, sales automation and other business.</p>
      <a class="btn">READ MORE <svg width="7" height="7" viewBox="0 0 8 8"><circle cx="4" cy="4" r="4" fill="#fff"/><path d="M3 2l2 2-2 2" stroke="#e8792a" fill="none"/></svg></a>
    </article>
  </section>

  <div class="abs tech">
    <span><i></i>Torvista</span>
    <span>QRX</span>
    <span>DataVane</span>
    <span><i></i>NCB</span>
  </div>

  <footer class="abs footer">
    <div class="badges"><div class="badge pale"></div><div class="badge"></div></div>
    <address>Address: Suite 42, Level 3|8 Wattlebrook Lane|Fernvale Heights VIC 3999<br>Phone number 1300 648 907<br>Email address : support@kavreo.example</address>
    <p class="copy">Copyright © 2016 Kavreo.All Rights Reserved</p>
  </footer>
</div>
</body>
</html>
```